Website Design for Gold Buying Company in Australia

We are looking for a Website layout for a company who buy gold pieces from trade and the public.

They would like to communicate that its easy, safe, a great way to make more money, and they pay the best prices in australia for Gold jewelery

Target Market(s)

Adults based in Australia aged 25-60 who are looking to make some extra money

Industry/Entity Type

It Company

Number of Pages Required

2 pages

Requirements
Must have
• Must have a homepage and a page to use for content.

• Will have a feed for the latest Gold, silver and platinum prices they are buying and selling at.

• Needs to have a from on the homepage where people can submit their details to be sent a ''Vaultpack'' which allows them to send gold pieces to eb valued and bought by the company.

Nice to have
• Would be nice to have a steped out graphic of how the ''Vaultpack by mail'' process works [Request a Kit, Send in your Gold, We Value and grade it, We pay you cash, cheque of Direct Deposit]

• Imagery will be gold related

• Colour schemes are not a major Issue-but using some gold or silver would be a good idea
Should not have
• No cheesy gold graphics please :)

```html
<!DOCTYPE html>
<html lang="en">
<head>
<meta charset="utf-8">
<title>Aurumbase – How it works</title>
<link href="https://fonts.googleapis.com/css2?family=Gelasio:ital,wght@0,400;0,700;1,400&family=Open+Sans:wght@400;600;700&display=swap" rel="stylesheet">
<style>
:root{
  --top-bar:#7d7b76;
  --header-top:#ffffff;
  --header-bottom:#f6e8bf;
  --nav-top:#b99a4a;
  --nav-bottom:#8a6e2c;
  --nav-active:#7a6130;
  --nav-trade:#e8b93c;
  --nav-text:#fff4d6;
  --gold:#c4951f;
  --gold-light:#f0c94a;
  --ink:#555;
  --ink-dark:#333;
  --muted:#9a9a9a;
  --panel:#7a7770;
  --panel-head:#8a8780;
  --title-bg:#f5f1eb;
  --title-line:#d8d2c6;
  --input-bg:#fffdf6;
  --footer-gold:#c9a233;
}
*{box-sizing:border-box;margin:0;padding:0}
html,body{width:1200px;height:756px;overflow:hidden;background:#fff}
body{position:relative;font-family:"Open Sans",Tahoma,sans-serif;color:var(--ink)}
.top-bar{position:absolute;left:0;top:0;width:1200px;height:6px;background:var(--top-bar)}
.site-header{position:absolute;left:0;top:6px;width:1200px;height:66px;background:linear-gradient(var(--header-top),var(--header-bottom));border-left:1px solid #e6d9b0;border-right:1px solid #e6d9b0}
.brand{position:absolute;left:232px;top:14px;font-family:"Gelasio",Georgia,serif;font-weight:700;font-size:30px;color:#6f6c66;letter-spacing:-.3px}
.brand-divider{position:absolute;left:543px;top:24px;width:1px;height:28px;background:#d9cfb4}
.tagline{position:absolute;left:556px;top:24px;font-family:"Gelasio",Georgia,serif;font-style:italic;font-size:16px;color:#a8a49b}
.search{position:absolute;left:766px;top:22px;width:166px;height:23px;border:1px solid #d6d1c4;background:#fff;font-size:10px;color:#777;padding:4px 6px}
.search-icon{position:absolute;left:937px;top:24px}
.main-nav{position:absolute;left:0;top:72px;width:1200px;height:33px;background:linear-gradient(var(--nav-top),var(--nav-bottom));border-bottom:2px solid #6e5825}
.main-nav a{position:absolute;top:0;height:33px;line-height:33px;font-size:12.5px;color:var(--nav-text);text-decoration:none;padding:0 10px}
.main-nav a.active{background:var(--nav-active)}
.main-nav a.trade{background:var(--nav-trade);color:#fff6dc}
.breadcrumb{position:absolute;left:232px;top:112px;font-size:8px;font-weight:700;color:#666}
.page-title{position:absolute;left:232px;top:130px;width:477px;height:38px;background:var(--title-bg);border:1px solid var(--title-line);padding:0 10px;font-family:"Gelasio",Georgia,serif;font-size:29px;line-height:36px;color:#6d6a64}
.page-title b{font-weight:700}
.content{position:absolute;left:232px;top:183px;width:477px}
.content h2{font-family:"Gelasio",Georgia,serif;font-style:italic;font-weight:400;font-size:18.5px;color:var(--gold);margin:0 0 14px}
.content p{font-size:9.6px;line-height:15px;text-align:justify;margin-bottom:15px}
.content p + h2{margin-top:23px}
.content strong{color:var(--ink-dark)}
.kit{position:absolute;left:725px;top:130px;width:231px;height:284px;background:var(--panel)}
.kit-head{height:50px;background:var(--panel-head);border-bottom:1px solid #6a675f;padding:2px 10px;font-family:"Gelasio",Georgia,serif;font-style:italic;font-size:33px;color:var(--gold-light)}
.kit-body{padding:11px 13px}
.kit-body h3{font-weight:400;font-size:13.2px;color:var(--gold-light);margin-bottom:14px}
.kit-body p{font-size:9.6px;line-height:15px;color:#f2f0ea;margin-bottom:12px}
.kit label{display:block;font-size:9.6px;font-weight:700;color:#e0ddd5;margin:0 0 6px 1px}
.kit .field{width:202px;height:20px;background:var(--input-bg);border:1px solid #c8c3b6;font-size:8.4px;padding:4px 5px;color:#555;margin-bottom:11px}
.send{position:absolute;left:165px;top:249px;width:50px;height:20px;background:linear-gradient(#f5cd55,#d6a429);border:1px solid #b0861e;font-family:"Gelasio",Georgia,serif;font-style:italic;font-weight:700;font-size:11px;color:#6a4f12;text-align:center;line-height:18px}
.site-footer{position:absolute;left:233px;top:662px;width:723px;height:51px;background:linear-gradient(#c79e2e 0,#c79e2e 26px,#d4ab3a 26px,#d4ab3a 45px,#7a6a3e 45px)}
.site-footer nav{position:absolute;left:0;top:29px;width:100%;text-align:center;font-size:8.6px}
.site-footer a{color:#5e4a1a;text-decoration:none;margin:0 7px}
.footer-url{position:absolute;left:0;top:716px;width:1200px;text-align:center;font-family:"Gelasio",Georgia,serif;font-size:19px;font-weight:700;color:#b39a5e}
</style>
</head>
<body>
<div class="top-bar"></div>
<header class="site-header">
  <div class="brand">Aurumbase.com.au</div>
  <div class="brand-divider"></div>
  <div class="tagline">Best prices in Australia</div>
  <div class="search">Search</div>
  <svg class="search-icon" width="20" height="20" viewBox="0 0 20 20" aria-hidden="true">
    <circle cx="8" cy="8" r="6" fill="#e9f2f8" stroke="#9aa6ad" stroke-width="2"/>
    <line x1="12.5" y1="12.5" x2="18" y2="18" stroke="#b0782a" stroke-width="3" stroke-linecap="round"/>
  </svg>
</header>
<nav class="main-nav">
  <a style="left:234px">About Us</a>
  <a style="left:311px">What we Buy &amp; Sell</a>
  <a class="active" style="left:449px;width:101px">How it works</a>
  <a style="left:553px">Commen Questions</a>
  <a style="left:691px">Bullion</a>
  <a style="left:754px">Contact Us</a>
  <a class="trade" style="left:842px;width:111px">Trade enquires</a>
</nav>
<div class="breadcrumb">Home</div>
<h1 class="page-title"><b>How it</b> works</h1>
<main class="content">
  <h2>1. Lorem ipsum dolor sit amet, consectetur adipiscing elit</h2>
  <p>Nulla malesuada elementum lorem, ac bibendum dui molestie et. Morbi mattis imperdiet auctor. Maecenas iaculis tincidunt venenatis. Etiam cursus vulputate turpis, sed ornare ligula commodo sit amet. Donec nunc erat, feugiat auctor elementum a, condimentum vitae urna. Fusce malesuada nisi nec dolor vestibulum pellentesque. Nullam vel turpis sit amet dui sollicitudin fringilla id sed dui. Vivamus commodo ornare velit quis dignissim. Pellentesque bibendum facilisis consectetur. Nam in mauris imperdiet dui laoreet scelerisque.</p>
  <h2>2. Curabitur id nibh diam, at accumsan odio</h2>
  <p>Phasellus nec nunc tincidunt velit congue dignissim consectetur eu odio. <strong>Sed nunc magna, congue eget pellentesque in, ullamcorper a nunc.</strong> In facilisis, mauris ac rhoncus posuere, mi nulla viverra nunc, non luctus erat orci non sem. Maecenas aliquet arcu a risus luctus id molestie leo porttitor. Suspendisse potenti. Cum sociis natoque penatibus et magnis dis parturient montes, nascetur ridiculus mus. Morbi a turpis id purus condimentum rutrum. Morbi scelerisque leo nulla, non aliquam mauris. Phasellus vel mi purus, eu convallis neque. Nulla faucibus tortor eget sem porta pulvinar.</p>
  <p>Nunc vel urna velit, a pretium massa. In hac habitasse platea dictumst. Phasellus sit amet nibh ac ipsum faucibus sagittis. Quisque dapibus scelerisque lacus ac dictum. Nullam tortor nulla, molestie nec accumsan quis, scelerisque vel massa. Cum sociis natoque penatibus et magnis dis parturient montes, nascetur ridiculus mus. Aliquam libero nibh, pulvinar sed interdum ut, consequat vel lorem. Pellentesque rutrum, lorem ut dignissim euismod, mi nibh fermentum nulla, non euismod eros sapien viverra mauris. Vestibulum id ante metus, quis pulvinar orci. Nunc sed velit urna, vitae porttitor diam. Fusce euismod orci nec erat porta eu ornare sapien posuere. Sed tincidunt consequat eros at auctor. Nunc mattis elit in purus gravida lobortis quis vel turpis.</p>
</main>
<aside class="kit">
  <div class="kit-head">Vaultpack</div>
  <div class="kit-body">
    <h3>Request a Kit, Send in your Gold</h3>
    <p>We Value and grade it, We pay you cash, cheque of Direct Deposit.</p>
    <label>Name</label>
    <div class="field">Mara Lindqvist</div>
    <label>E-mail</label>
    <div class="field">mara.l@example.com</div>
  </div>
  <div class="send">Send »</div>
</aside>
<footer class="site-footer">
  <nav>
    <a>About Us</a><a>What we Buy &amp; Sell</a><a>How it works</a><a>Commen Questions</a><a>Bullion</a><a>Contact Us</a><a>Trade enquires</a>
  </nav>
</footer>
<div class="footer-url">www.aurumbase.com.au</div>
</body>
</html>
```